Landing Page and Logo for Auto-Blogging Platform

I created a platform that allows users to start a blog for their business, hobby, charity, etc. I need a landing page where users can learn about the platform, benefits of consistent blogging, SEO value, plans/pricing, etc. The landing page needs to have multiple call to action buttons encouraging the visitor to register/sign up for a free trial.

In addition to the landing page, I need a page for users to establish the settings for their blog. This page should be a fairly simple form, intended for the user to enter a few details to set up their blog:
1. Name of Blog
2. Up to 10 topics and/or keywords the blog should focus on
3. Theme: Color-scheme and logo upload for blog.

I have attached the specifications of the platform's functionality so you can better understand how it works, plans/pricing, etc.

I also need a logo for the business. The name of the platform is PostNook.

Target Market(s)

Website owners, bloggers, business owners

Industry/Entity Type

Technology, Internet, web design

Coding

Coded - Design and coding required

Number of Pages Required

2 page

Colors
0054AA
0677BA
7BADD7
CADEEF
E8F1F8
0094D4
00A9DD
6FCCEA
C7EBF8
E9F6FB

Requirements
Must have
• Eye-catching design but fairly light on content (keep it simple and brief.)
Nice to have
• Eye-catching yet simple design, clean and easy to understand what we are offering.
Should not have
• Too much “wordy” and confusing content.

```html
<!DOCTYPE html>
<html lang="en">
<head>
<meta charset="utf-8">
<title>PostNook – Auto-Blogging Platform</title>
<link href="https://fonts.googleapis.com/css2?family=Poppins:wght@600;700;800&family=Roboto:wght@400;500;700&display=swap" rel="stylesheet">
<style>
:root{
  --blue-deep:#0054AA;
  --blue-mid:#0677BA;
  --blue-soft:#7BADD7;
  --blue-pale:#CADEEF;
  --blue-mist:#E8F1F8;
  --cyan:#0094D4;
  --cyan-bright:#00A9DD;
  --cyan-soft:#6FCCEA;
  --cyan-pale:#C7EBF8;
  --text:#2b2b2b;
  --muted:#555;
  --white:#fff;
}
*{margin:0;padding:0;box-sizing:border-box}
html,body{width:1200px;height:2933px;overflow:hidden}
body{position:relative;background:var(--white);font-family:'Roboto',sans-serif;color:var(--text)}
.abs{position:absolute}
.btn{position:absolute;display:flex;align-items:center;justify-content:center;border-radius:24px;color:var(--white);font-family:'Roboto',sans-serif;font-weight:700;font-size:13px;letter-spacing:-.2px;text-transform:uppercase;background:var(--blue-deep)}
.btn--light{background:var(--blue-soft)}
.btn--cyan{background:var(--cyan-bright)}

/* header */
.site-header{position:absolute;left:0;top:0;width:1200px;height:85px;border-top:4px solid var(--blue-mid);background:var(--white);box-shadow:0 1px 3px rgba(0,0,0,.06)}
.brand{position:absolute;left:145px;top:14px;display:flex;align-items:center;gap:8px}
.brand__dot{width:48px;height:48px;border-radius:50%;background:var(--blue-mid)}
.brand__name{font-family:'Poppins',sans-serif;font-weight:800;font-size:40px;color:var(--blue-deep);letter-spacing:-1px}
.nav{position:absolute;top:36px;font-size:14px;font-weight:500;color:#222}
.nav__active::after{content:"";display:inline-block;width:7px;height:7px;border-radius:50%;background:var(--cyan);margin-left:6px;vertical-align:middle}

/* hero */
.hero-photo{position:absolute;left:0;top:85px;width:1200px;height:516px;background:linear-gradient(120deg,#6b4a34 0%,#8a6446 30%,#5d5a58 55%,#9a9ea4 75%,#c9c6c0 100%)}
.hero-card{position:absolute;left:145px;top:188px;width:466px;height:313px;background:var(--blue-deep);border-top-left-radius:70px}
.hero-card h1{position:absolute;left:80px;top:32px;font-family:'Poppins',sans-serif;font-weight:800;font-size:70px;color:var(--white);letter-spacing:-1.5px;line-height:1}
.hero-card p{position:absolute;left:80px;top:135px;width:340px;font-size:15.5px;line-height:22px;color:var(--white)}
.slider-dot{position:absolute;left:57px;width:8px;height:8px;border-radius:50%;background:var(--white)}
.slider-dot--on{width:12px;height:12px;left:55px;border:2px solid var(--white);background:var(--blue-soft)}

/* how it works */
.how-bg{position:absolute;left:0;top:820px;width:1200px;height:575px;background:linear-gradient(180deg,#fff 0%,#eef1f4 35%,#dfe4ea 70%,#f4f6f8 100%)}
.section-title{position:absolute;font-family:'Poppins',sans-serif;font-weight:800;color:var(--blue-deep);letter-spacing:-1px;line-height:1.15}
.underline{position:absolute;height:4px;border-radius:2px;background:var(--cyan)}
.how-sub{position:absolute;left:0;width:1200px;top:752px;text-align:center;font-size:18px;color:#222}
.step-num{position:absolute;font-family:'Poppins',sans-serif;font-weight:600;font-size:118px;line-height:1;color:transparent;-webkit-text-stroke:3px var(--blue-mid)}
.step-ring{position:absolute;width:124px;height:124px;border-radius:50%;border:3px solid var(--blue-mid);background:var(--white);display:flex;align-items:center;justify-content:center}
.step-ring::before{content:"";position:absolute;left:4px;top:4px;width:12px;height:12px;border-radius:50%;background:var(--cyan-soft);border:2px solid var(--white)}
.step-core{width:92px;height:92px;border-radius:50%;background:var(--blue-deep);display:flex;align-items:center;justify-content:center}
.step-caption{position:absolute;text-align:center;font-size:16.5px;line-height:20px;color:#222}
.how-note{position:absolute;left:195px;top:1138px;width:810px;text-align:center;font-size:15px;line-height:25px;color:#333}

/* about */
.about{position:absolute;left:55px;top:1395px;width:1145px;height:628px;background:var(--blue-mist);border-top-left-radius:70px}
.about-shots{position:absolute;left:142px;top:1471px;width:321px;height:476px;background:linear-gradient(160deg,#f3f5f8,#d7dde6 40%,#9aa8b8 70%,#e9ecf0)}
.about-text{position:absolute;left:537px;top:1606px;width:516px;font-size:14.5px;line-height:24.8px;color:#444;text-align:justify}

/* pricing */
.pricing-intro{position:absolute;left:511px;top:2095px;width:540px;font-size:14.5px;line-height:25px;color:#444}
.mountain{position:absolute;left:0;width:1200px;background:linear-gradient(180deg,#fff 0%,#e7ebef 30%,#9aa4ae 60%,#5f6a75 80%,#cfd6dd 100%)}
.plan{position:absolute;top:2214px;width:296px;height:232px;background:var(--white);border:2px solid #d8dfe6;border-top-left-radius:55px;text-align:center}
.plan--featured{background:#f3f7fb;box-shadow:6px 6px 10px rgba(0,60,120,.15)}
.plan h3{margin-top:24px;font-family:'Roboto',sans-serif;font-weight:500;font-size:24px;color:var(--blue-deep)}
.plan p{margin:14px auto 0;width:270px;font-size:15.5px;line-height:21px;color:#333}
.plan__price{margin-top:12px;font-weight:700;font-size:23px;color:var(--cyan)}
.plan .btn{left:92px;top:168px;width:110px;height:40px;font-size:12px}

/* footer */
.site-footer{position:absolute;left:0;top:2683px;width:1200px;height:250px;background:var(--blue-deep);color:var(--white)}
.contact{position:absolute;top:50px;display:flex;align-items:center;gap:18px}
.contact__icon{width:54px;height:54px;border-radius:50%;background:var(--white);display:flex;align-items:center;justify-content:center}
.contact__icon--mail{background:#e09a2c}
.contact h4{font-weight:500;font-size:17px}
.contact span{font-size:15px}
.copyright{position:absolute;left:0;width:1200px;top:140px;text-align:center;font-size:14px}
.social{position:absolute;top:182px;width:28px;height:28px;border-radius:50%;border:2.5px solid var(--white)}
</style>
</head>
<body>

<header class="site-header">
  <div class="brand"><span class="brand__dot"></span><span class="brand__name">PostNook</span></div>
  <span class="nav nav__active" style="left:461px">HOME</span>
  <span class="nav" style="left:535px">PRICING</span>
  <span class="nav" style="left:624px">HOW IT WORKS</span>
  <span class="nav" style="left:758px">CONTACT</span>
  <span class="btn" style="left:856px;top:21px;width:198px;height:43px">Sign up for a free trial</span>
</header>

<section>
  <div class="hero-photo" role="img" aria-label="Desk scene with a laptop showing a blog, coffee cup, notebooks and glasses"></div>
  <div class="hero-card">
    <h1>PostNook</h1>
    <p>The purpose of this platform is to allow anyone to start a blog and automate the process of creating content and posting it to the blog.</p>
    <span class="btn btn--light" style="left:80px;top:234px;width:197px;height:42px">Sign up for a free trial</span>
  </div>
  <span class="slider-dot" style="top:506px"></span>
  <span class="slider-dot" style="top:521px"></span>
  <span class="slider-dot slider-dot--on" style="top:535px"></span>
</section>

<section>
  <div class="how-bg" role="img" aria-label="Faint snowy mountain peak in the background"></div>
  <h2 class="section-title" style="left:0;width:1200px;text-align:center;top:678px;font-size:46px">How It Works</h2>
  <p class="how-sub">The blog topics can be created using any of these methods</p>
  <span class="underline" style="left:576px;top:792px;width:48px"></span>

  <svg class="abs" style="left:0;top:850px" width="1200" height="160" viewBox="0 0 1200 160" fill="none">
    <path d="M316 50 C370 10 440 10 492 70" stroke="#888" stroke-width="2" stroke-dasharray="2 5"/>
    <path d="M482 58 L494 74 L476 72 Z" fill="#888"/>
    <path d="M690 108 C740 150 820 150 868 110" stroke="#888" stroke-width="2" stroke-dasharray="2 5"/>
    <path d="M856 108 L872 106 L864 120 Z" fill="#888"/>
  </svg>

  <span class="step-num" style="left:140px;top:868px">1</span>
  <div class="step-ring" style="left:177px;top:870px"><div class="step-core">
    <svg width="40" height="40" viewBox="0 0 40 40" fill="#fff"><circle cx="20" cy="12" r="8"/><path d="M5 36c0-9 6-14 15-14s15 5 15 14z"/></svg>
  </div></div>
  <p class="step-caption" style="left:159px;top:1018px;width:160px">The user enters them into a table manuall</p>

  <span class="step-num" style="left:500px;top:868px">2</span>
  <div class="step-ring" style="left:547px;top:870px">
    <svg width="56" height="56" viewBox="0 0 56 56" fill="none" stroke="#0054AA" stroke-width="5" stroke-linecap="round" stroke-linejoin="round"><path d="M28 40V14M17 25l11-11 11 11"/><path d="M12 46h32"/></svg>
  </div>
  <p class="step-caption" style="left:509px;top:1014px;width:200px">The user uploads a list of blog topics in CSV forma</p>

  <span class="step-num" style="left:874px;top:868px">3</span>
  <div class="step-ring" style="left:923px;top:870px">
    <svg width="60" height="50" viewBox="0 0 60 50" fill="#0054AA"><rect x="23" y="2" width="14" height="11"/><rect x="4" y="36" width="14" height="11"/><rect x="23" y="36" width="14" height="11"/><rect x="42" y="36" width="14" height="11"/><path d="M29 13h2v10h19v13h-2V25H31v11h-2V25H12v11h-2V23h19z"/></svg>
  </div>
  <p class="step-caption" style="left:834px;top:1012px;width:230px">AI can create the list of blog topics based on a prompt such as: “Provide a list of 52 blog topics for a handyman business’s blog.”</p>

  <p class="how-note">There should also be an option for the user to generate a blog post instantly (outside of their regularly-scheduled auto-posts) if they are on the Ultimate Plan. I will choose a domain name for the platform. Each user will receive a subdomain (such as woodshop.postnookhq.com) or a path from the root domain (such as postnookhq.com/woodshop). The subdomain would be preferred, but the path option would also be acceptable, if necessary</p>
  <span class="btn" style="left:496px;top:1269px;width:208px;height:43px">Sign up for a free trial</span>
</section>

<section>
  <div class="about"></div>
  <div class="about-shots" role="img" aria-label="Collection of blog and newsletter page layouts"></div>
  <h2 class="section-title" style="left:537px;top:1462px;font-size:47px">About<br>The Platform</h2>
  <span class="underline" style="left:537px;top:1577px;width:48px"></span>
  <p class="about-text">There needs to be a super-admin panel where platform owner/administrator can see users, their activity, manage user access, etc.Each user will have a dashboard where they control their settings such as account information, billing, view blog posts, view blog post topics, etc. From this dashboard, the user can customize the “look and feel” of their blog including theme, hero banner, header, footer, logo, color scheme, etc.The platform will require a list of blog topics. Based on the topics list, the software will need to automatically send prompts to TextMind in the specified intervals (monthly, weekly, or daily), receive the blog content, and post it to the blog. Furthermore, the software will need some method of adding at least one image to each blog post. Ideally, this would be achieved by using the PhotoVault API to retrieve image(s) based on keywords in the blog topic</p>
  <span class="btn" style="left:537px;top:1901px;width:119px;height:42px">Read more</span>
</section>

<section>
  <h2 class="section-title" style="left:146px;top:2085px;font-size:48px">Pricing Plan</h2>
  <span class="underline" style="left:146px;top:2148px;width:48px"></span>
  <p class="pricing-intro">SAAS model. The platform can be used to sell unique accounts to multiple users. There must be a subscription plan and a 14-day free trial. The subscriptions are:</p>

  <div class="mountain" style="top:2290px;height:393px" role="img" aria-label="Snowy mountain range"></div>

  <div class="plan" style="left:143px">
    <h3>Base Plan</h3>
    <p>1 blog post (up to 2,000 words) every month</p>
    <div class="plan__price">$9.99/mo</div>
    <span class="btn">View plan</span>
  </div>
  <div class="plan plan--featured" style="left:452px">
    <h3>Premium Plan</h3>
    <p>1 blog post (up to 2,000 words) every week</p>
    <div class="plan__price">$14.99/mo</div>
    <span class="btn btn--cyan">View plan</span>
  </div>
  <div class="plan" style="left:760px">
    <h3>Ultimate Plan</h3>
    <p>1 blog post (up to 3,000 words) per day plus unlimited manual posting</p>
    <div class="plan__price">$24.99/mo</div>
    <span class="btn">View plan</span>
  </div>
</section>

<footer class="site-footer">
  <div class="contact" style="left:210px">
    <span class="contact__icon"><svg width="22" height="26" viewBox="0 0 22 26"><path d="M11 1C5.5 1 2 5 2 10c0 6 9 15 9 15s9-9 9-15c0-5-3.5-9-9-9z" fill="#0054AA"/><circle cx="11" cy="10" r="3.5" fill="#fff"/></svg></span>
    <div><h4>Location</h4><span>48 Harbor Lane, Suite 2</span></div>
  </div>
  <div class="contact" style="left:519px">
    <span class="contact__icon contact__icon--mail"><svg width="26" height="20" viewBox="0 0 26 20"><rect x="1" y="1" width="24" height="18" rx="2" fill="#fff"/><path d="M2 3l11 8 11-8" stroke="#e09a2c" stroke-width="2" fill="none"/></svg></span>
    <div><h4>Email</h4><span>hello@postnookmail.com</span></div>
  </div>
  <div class="contact" style="left:803px">
    <span class="contact__icon"><svg width="24" height="24" viewBox="0 0 24 24"><path d="M6 2l4 5-2 3c1.5 3 3 4.5 6 6l3-2 5 4-2 4C10 22 2 14 2 4z" fill="#0054AA"/></svg></span>
    <div><h4>CALL US</h4><span>+1 555 014 2233</span></div>
  </div>
  <p class="copyright">© 2024 PostNook – All Rights Reserved &nbsp;| &nbsp;Privacy &nbsp;Policy &nbsp;| &nbsp;Terms of Use</p>
  <span class="social" style="left:546px" aria-label="Social profile"></span>
  <span class="social" style="left:587px" aria-label="Messaging profile"></span>
  <span class="social" style="left:628px" aria-label="Professional profile"></span>
</footer>

</body>
</html>
```